Varnik Holdings — Business Card Design Brief
Overview
Design a double-sided business card for Varnik Holdings that highlights our two service arms: Varnik Communications (telecommunications) and Varnik Energy (business energy solutions). The card should feel smart and stand out when handed to clients.

Objectives
Showcase our areas of specialty clearly.
Reflect the overall Varnik / Varnik Holdings brand while acknowledging both arms.
Explore using both logos (Communications + Energy) or one unified logo, depending on the design.

Deliverables
One double-sided business card design (front + back).

Content & Copy
Front (preferred): Logo: Varnik / Varnik Holdings
Descriptor: Business Communications | Business Energy
Back:My contact details and company details
Core products: Business Mobile • Telephony • Internet • Business Energy Solutions

Brand & Visual Direction
We have a group logo currently tailored more toward telecoms, plus a separate Varnik Energy logo.
Please explore layouts that use both logos or just one, whichever works best.
Color: I wouldn't mind seeing an option using our the Blue/Purple gradient from our website (varnik-example.co.uk), but also open to non-gradient approaches and other colours..

Overall look: Smart, modern, and distinctive.
Format & Print Specs
Double-sided business card format. (Use a standard size

Must-Haves
Front: Varnik wording or Varnik Holdings wording with atleast 1 logo also on front “Business Communications | Business Energy.”

Back: Contact + company details and core products.
A design that stands out while remaining professional.

Nice-to-Have Options
A gradient version using our site’s Blue/Purple gradient.
A non-gradient version.
A dual-logo treatment versus a single-logo treatment.

Thanks
Owen

```html
<!DOCTYPE html>
<html lang="en">
<head>
<meta charset="utf-8">
<title>Varnik Holdings — Business Card</title>
<link rel="stylesheet" href="https://fonts.googleapis.com/css2?family=Poppins:wght@400;500;700&display=swap">
<style>
  :root {
    --stage: #222222;
    --card: #ffffff;
    --navy: #1f1b5c;
    --blue: #2b5fb5;
    --purple: #7e3a9c;
    --green: #2eaa4a;
    --lime: #9bc53d;
    --yellow: #d6d91f;
    --ink: #1a1a2e;
  }
  * { box-sizing: border-box; margin: 0; padding: 0; }
  html, body { width: 1200px; height: 800px; overflow: hidden; }
  body {
    background: var(--stage);
    font-family: "Poppins", sans-serif;
    color: var(--ink);
    position: relative;
  }
  .card {
    position: absolute;
    left: 300px;
    width: 600px;
    height: 343px;
    background: var(--card);
    border-radius: 22px;
    overflow: hidden;
    box-shadow: -4px 5px 0 var(--green), 0 12px 30px rgba(0,0,0,.5);
  }
  .card--front { top: 28px; }
  .card--back { top: 418px; }

  /* Front */
  .front-mark {
    position: absolute;
    left: 0; right: 0; top: 105px;
    display: flex; justify-content: center; align-items: center; gap: 16px;
  }
  .mark-dot {
    width: 46px; height: 46px; border-radius: 50%;
    background: var(--blue);
  }
  .wordmark {
    font-weight: 700;
    font-size: 64px;
    letter-spacing: 2px;
    color: var(--navy);
    line-height: 1;
  }
  .descriptor {
    position: absolute;
    left: 0; right: 0; bottom: 62px;
    text-align: center;
    font-size: 15px;
    font-weight: 500;
    color: var(--navy);
    letter-spacing: .5px;
  }
  .edge-bands { position: absolute; inset: 0; pointer-events: none; }

  /* Back */
  .name-accent {
    position: absolute; left: 0; top: 40px;
    width: 10px; height: 52px;
    background: linear-gradient(var(--yellow), var(--lime));
  }
  .person { position: absolute; left: 30px; top: 34px; }
  .person-name {
    font-size: 30px; font-weight: 700; line-height: 1.1;
  }
  .person-name .first { color: var(--purple); }
  .person-name .last { color: var(--blue); }
  .person-role { font-size: 14px; font-weight: 500; color: var(--ink); }

  .back-mark {
    position: absolute; right: 32px; top: 38px;
    display: flex; align-items: center; gap: 12px;
  }
  .back-mark .mark-dot { background: var(--green); width: 40px; height: 40px; }
  .back-mark .wordmark { font-size: 46px; }

  .services {
    position: absolute; left: 360px; top: 122px;
    list-style: none;
    font-size: 14px; line-height: 1.55;
  }
  .services li { display: flex; align-items: center; gap: 9px; }
  .services li::before {
    content: ""; width: 8px; height: 8px; border-radius: 50%;
    background: linear-gradient(135deg, var(--purple), var(--blue));
    flex: none;
  }

  .address {
    position: absolute; left: 56px; top: 160px;
    font-size: 14px; line-height: 1.4;
  }
  .contacts {
    position: absolute; left: 56px; top: 214px;
    list-style: none; font-size: 14px; line-height: 1.6;
  }
  .contacts li { display: flex; align-items: center; gap: 10px; }
  .contacts svg { width: 15px; height: 15px; flex: none; }
</style>
</head>
<body>

  <section class="card card--front" aria-label="Card front">
    <div class="front-mark">
      <span class="mark-dot" aria-hidden="true"></span>
      <span class="wordmark">VARNIK</span>
    </div>
    <p class="descriptor">Business Communications | Business Energy</p>
  </section>

  <section class="card card--back" aria-label="Card back">
    <span class="name-accent" aria-hidden="true"></span>
    <div class="person">
      <h1 class="person-name"><span class="first">Mira</span> <span class="last">Kellan</span></h1>
      <p class="person-role">Founder &amp; CEO</p>
    </div>

    <div class="back-mark">
      <span class="mark-dot" aria-hidden="true"></span>
      <span class="wordmark">VARNIK</span>
    </div>

    <ul class="services">
      <li>Business Mobile</li>
      <li>Telephony</li>
      <li>Internet</li>
      <li>Business Energy Solutions</li>
    </ul>

    <p class="address">24 Elm Row, Northbridge,<br>England, NB2 7QX</p>

    <ul class="contacts">
      <li>
        <svg viewBox="0 0 24 24" aria-hidden="true"><path fill="#7e3a9c" d="M6.6 10.8a15 15 0 0 0 6.6 6.6l2.2-2.2a1 1 0 0 1 1-.25 11.4 11.4 0 0 0 3.6.57 1 1 0 0 1 1 1V20a1 1 0 0 1-1 1A17 17 0 0 1 3 4a1 1 0 0 1 1-1h3.5a1 1 0 0 1 1 1c0 1.25.2 2.45.57 3.57a1 1 0 0 1-.25 1z"/></svg>
        +44 0100 555 0142
      </li>
      <li>
        <svg viewBox="0 0 24 24" aria-hidden="true"><circle cx="12" cy="12" r="9" fill="none" stroke="#2b5fb5" stroke-width="2"/><path d="M3 12h18M12 3c3 3 3 15 0 18M12 3c-3 3-3 15 0 18" fill="none" stroke="#2b5fb5" stroke-width="1.6"/></svg>
        www.varnik-example.co.uk
      </li>
      <li>
        <svg viewBox="0 0 24 24" aria-hidden="true"><rect x="3" y="6" width="18" height="13" rx="1.5" fill="none" stroke="#7e3a9c" stroke-width="2"/><path d="M3 7l9 7 9-7" fill="none" stroke="#7e3a9c" stroke-width="2"/></svg>
        info@varnik-example.co.uk
      </li>
    </ul>

    <svg class="edge-bands" viewBox="0 0 600 343" preserveAspectRatio="none" aria-hidden="true">
      <defs>
        <linearGradient id="band-brand" x1="0" x2="1" y1="0" y2="0">
          <stop offset="0" stop-color="#7e3a9c"/>
          <stop offset="0.6" stop-color="#2b5fb5"/>
          <stop offset="1" stop-color="#1f1b5c"/>
        </linearGradient>
        <linearGradient id="band-energy" x1="0" x2="1" y1="0" y2="0">
          <stop offset="0" stop-color="#2eaa4a"/>
          <stop offset="1" stop-color="#d6d91f"/>
        </linearGradient>
      </defs>
      <polygon points="430,262 600,210 600,262" fill="url(#band-energy)"/>
      <polygon points="0,343 0,332 480,270 600,270 600,343" fill="url(#band-brand)"/>
      <polygon points="0,332 0,329 470,266 490,266" fill="#d6d91f"/>
    </svg>
  </section>

</body>
</html>
```